Realty Group Needs Classy, Contemporary Letterhead Design

We need a letterhead design for a new realty company located in NY, USA. We buy investment properties to rehabilitate and or keep in our rental portfolio.

```html
<!DOCTYPE html>
<html lang="en">
<head>
<meta charset="utf-8">
<title>Meridale Realty Group – Letterhead</title>
<link rel="stylesheet" href="https://fonts.googleapis.com/css2?family=Open+Sans:wght@400;600&family=Allura&display=swap">
<style>
  :root {
    --bg: #bdbdbd;
    --paper: #ffffff;
    --brand: #4b2a88;
    --rule: #6e6e6e;
    --text: #9a9a9a;
    --text-dark: #6a6a6a;
  }
  * { box-sizing: border-box; margin: 0; padding: 0; }
  html, body { width: 1200px; height: 795px; overflow: hidden; }
  body {
    background: var(--bg);
    font-family: "Open Sans", Arial, sans-serif;
    display: flex; align-items: center; justify-content: center;
  }
  .letterhead {
    position: relative;
    width: 540px; height: 763px;
    background: var(--paper);
    box-shadow: 0 6px 18px rgba(0,0,0,.18);
    color: var(--text);
    font-size: 9.5px; line-height: 1.5;
    overflow: hidden;
  }
  .brand {
    position: absolute; left: 44px; top: 52px;
    display: flex; align-items: center; gap: 6px;
  }
  .brand-mark { width: 12px; height: 12px; background: var(--brand); }
  .brand-name {
    font-weight: 600; font-size: 14px; line-height: 1; color: var(--brand);
  }
  .contact {
    position: absolute; right: 44px; top: 44px;
    font-size: 7.5px; line-height: 1.55; color: var(--text-dark);
  }
  .contact li { list-style: none; display: flex; align-items: center; gap: 4px; }
  .contact .dot { width: 7px; height: 7px; border-radius: 50%; background: var(--brand); }
  .letter { position: absolute; left: 44px; top: 150px; width: 430px; }
  .letter p { margin-bottom: 12px; text-align: justify; }
  .salutation { color: var(--text-dark); font-weight: 600; }
  .signature {
    font-family: "Allura", cursive; font-size: 28px; color: var(--text);
    line-height: 1; margin: 2px 0 4px;
  }
  .footer { position: absolute; left: 0; bottom: 0; width: 540px; height: 120px; }
  .footer svg { position: absolute; left: 0; top: 0; }
  .footer-url {
    position: absolute; right: 0; top: 50px;
    width: 150px; height: 24px; line-height: 24px;
    text-align: center;
    font-size: 8px; color: var(--paper); font-weight: 600;
  }
</style>
</head>
<body>
<main class="letterhead">
  <header>
    <div class="brand">
      <span class="brand-mark"></span>
      <span class="brand-name">Meridale Realty Group, LLC</span>
    </div>
    <ul class="contact">
      <li>Suite 103 Street name,</li>
      <li>State, Zip 2034, Country</li>
      <li><span class="dot"></span>000 0123 567 890</li>
      <li><span class="dot"></span>000 0123 567 891</li>
      <li><span class="dot"></span>hello@meridalerealtygroup.com</li>
    </ul>
  </header>

  <section class="letter">
    <p>January 12, 2014</p>
    <p>Mr. John Doe<br>President<br>AA Corporation<br>111 Street Name, Suite#<br>City, State, 12345</p>
    <p class="salutation">Dear Mr. John,</p>
    <p>Lorem Ipsum is simply dummy text of the printing and typesetting industry. Lorem Ipsum has been the industry's standard dummy text ever since the 1500s, when an unknown printer took a galley of type and scrambled it to make a type specimen book. It has survived not only five centuries, but also the leap into electronic typesetting, remaining essentially unchanged.</p>
    <p>The standard chunk of Lorem Ipsum used since the 1500s is reproduced below for those interested. Sections 1.10.32 and 1.10.33 from "de Finibus Bonorum et Malorum" by Cicero are also reproduced in their exact original form, accompanied by English versions from the 1914 translation by H. Rackham.</p>
    <p>Lorem Ipsum is simply dummy text of the printing and typesetting industry. Lorem Ipsum has been the industry's standard dummy text ever since the 1500s, when an unknown printer took a galley of type and scrambled it to make a type specimen book. It has survived not only five centuries, but also the leap into electronic typesetting, remaining essentially unchanged. It was popularised in the</p>
    <p style="margin-bottom:0">Sincerely Your,</p>
    <div class="signature">your name</div>
    <p>Name Last Name<br>Company Name</p>
  </section>

  <footer class="footer">
    <svg width="540" height="120" viewBox="0 0 540 120" aria-hidden="true">
      <path d="M0 104 L330 104 Q342 104 350 96 L372 74 Q380 66 392 66 L540 66 L540 120 L0 120 Z" fill="var(--rule)"/>
      <path d="M0 108 L332 108 Q346 108 355 99 L377 78 Q385 70 396 70 L540 70 L540 120 L0 120 Z" fill="var(--paper)"/>
      <path d="M0 111 L334 111 Q349 111 358 102 L380 82 Q388 74 400 74 L540 74 L540 120 L0 120 Z" fill="var(--brand)"/>
      <path d="M392 74 Q384 74 380 62 L378 56 Q376 50 384 50 L540 50 L540 74 Z" fill="var(--rule)"/>
    </svg>
    <span class="footer-url">www.meridalerealtygroup.com</span>
  </footer>
</main>
</body>
</html>
```